Tech Savy small Business accountant business card design

We need a business card for a new company based in the cloud. We provide tax, business advisory, accounting, information technology solutions and back office functions to small businesses. We offer fixed fee packages with add on services as you need them. By harnessing technology we simplify small business operational processes providing valuable time and information for small business owners to grow their business. In the logo (bluvoria) we want to be able to see bluv and experts. The final design should communicate achieving growth dreams and balance (ie life and $).
Updates
This project has been temporarily placed on hold until I finalize "Tech Savy small Business accountant needs a logo". I invite all designers to submit on this logo project. Once my logo is finalized I will resume this business card contest. Thanks Added Wednesday, March 19, 2014
This project has been temporarily placed on hold until I finalize "Tech Savy small Business accountant logo". I invite all designers to submit on this logo project. Once my logo is finalized I will resume this business card contest. Thanks Added Thursday, March 20, 2014
Target Market(s)
Small Business (Revenue $500,000, more than 3 employees) owners.
Industry/Entity Type
Small Business
Contact Information for Business Card
Marcy Elwind (Principal)
Accountant, Tax Agent.
TEL | 0417 683 912
EMAIL | Marcy.Elwind@bluvoria.com.au
WEB | www.bluvoria.com.au
Look and feel

```html
<!DOCTYPE html>
<html lang="en">
<head>
<meta charset="utf-8">
<title>Bluvoria business card</title>
<link href="https://fonts.googleapis.com/css2?family=Open+Sans:wght@400;600;700;800&display=swap" rel="stylesheet">
<style>
  :root {
    --page: #eceef1;
    --card-white: #ffffff;
    --brand-blue: #1e86cf;
    --brand-blue-light: #5cc0ee;
    --brand-blue-deep: #0f63b5;
    --ink: #1d1f24;
    --ink-soft: #33363c;
    --rule: #4aa6de;
  }
  * { box-sizing: border-box; margin: 0; padding: 0; }
  html, body { width: 1200px; height: 913px; overflow: hidden; }
  body {
    background: var(--page);
    font-family: "Open Sans", Arial, sans-serif;
    position: relative;
  }
  .card {
    position: absolute;
    width: 560px;
    height: 320px;
    border-radius: 16px;
    overflow: hidden;
    box-shadow: 0 6px 18px rgba(0,0,0,0.12);
  }
  /* Front */
  .card-front { left: 90px; top: 90px; background: var(--card-white); }
  .front-band {
    position: absolute; left: 14px; top: 0; bottom: 0; width: 58px;
    background: linear-gradient(180deg, var(--brand-blue-light), var(--brand-blue));
  }
  .front-corner {
    position: absolute; right: 0; top: 0; width: 18px; height: 22px;
    background: var(--ink);
  }
  .front-brand {
    position: absolute; right: 36px; top: 26px; text-align: right;
  }
  .wordmark {
    font-weight: 800; letter-spacing: -1px; line-height: 1;
  }
  .front-brand .wordmark { font-size: 44px; color: var(--brand-blue); }
  .front-brand .tagline { font-size: 13px; color: var(--ink-soft); margin-top: 2px; }
  .person {
    position: absolute; right: 36px; top: 128px; text-align: right;
  }
  .person-name { font-size: 20px; font-weight: 700; color: var(--ink); letter-spacing: 0.3px; }
  .person-role { font-size: 13px; color: var(--brand-blue); margin-top: 1px; }
  .front-rule {
    position: absolute; left: 72px; right: 36px; top: 180px; height: 1px;
    background: var(--rule);
  }
  .contacts {
    position: absolute; right: 36px; top: 192px; list-style: none; text-align: right;
    font-size: 12.5px; color: var(--ink-soft); line-height: 20px;
  }
  .contacts li { display: flex; justify-content: flex-end; align-items: center; gap: 6px; }
  .contacts svg { width: 12px; height: 12px; flex: none; }
  /* Back */
  .card-back {
    left: 560px; top: 500px;
    background: linear-gradient(160deg, var(--brand-blue-light) 0%, var(--brand-blue) 55%, var(--brand-blue-deep) 100%);
  }
  .back-band {
    position: absolute; right: 14px; top: 0; bottom: 0; width: 58px;
    background: var(--card-white);
  }
  .back-brand {
    position: absolute; left: 48px; top: 104px;
  }
  .back-brand .wordmark { font-size: 72px; color: var(--card-white); }
  .back-brand .tagline { font-size: 19px; font-weight: 600; color: var(--ink); margin-top: 4px; }
</style>
</head>
<body>
  <section class="card card-front" aria-label="Business card front">
    <div class="front-band"></div>
    <div class="front-corner"></div>
    <div class="front-brand">
      <div class="wordmark">bluvoria</div>
      <div class="tagline">Your business and accounting partner</div>
    </div>
    <div class="person">
      <div class="person-name">MARCY ELWIND (Principal)</div>
      <div class="person-role">Accountant, Tax Agent</div>
    </div>
    <div class="front-rule"></div>
    <ul class="contacts">
      <li>0417 683 912
        <svg viewBox="0 0 12 12"><path d="M3 1l2 2.5-1.2 1.2a6 6 0 0 0 3.5 3.5L8.5 7 11 9l-1.3 2C5.5 11 1 6.5 1 2.3z" fill="#1e86cf"/></svg>
      </li>
      <li>www.bluvoria.com.au
        <svg viewBox="0 0 12 12"><circle cx="6" cy="6" r="5" fill="none" stroke="#1e86cf" stroke-width="1.2"/><path d="M1 6h10M6 1c-2.5 3-2.5 7 0 10M6 1c2.5 3 2.5 7 0 10" fill="none" stroke="#1e86cf" stroke-width="1"/></svg>
      </li>
      <li>Marcy.Elwind@bluvoria.com.au
        <svg viewBox="0 0 12 12"><rect x="1" y="2.5" width="10" height="7" fill="none" stroke="#1e86cf" stroke-width="1.2"/><path d="M1 2.5l5 4 5-4" fill="none" stroke="#1e86cf" stroke-width="1.2"/></svg>
      </li>
    </ul>
  </section>

  <section class="card card-back" aria-label="Business card back">
    <div class="back-band"></div>
    <div class="back-brand">
      <div class="wordmark">bluvoria</div>
      <div class="tagline">Your business and accounting partner</div>
    </div>
  </section>
</body>
</html>
```